Tinned Food Label Design

We are after 5 Labels for tinned food
1: Diced Tomato's 425g
2: Baked Beans 425g
3: Two Fruits (Peach & Pear) 820g
4: Sliced Peaches 820g
5: Mixed Vegetables (Peas, Carrots and Corn) 425g

we will supply Nutritional Information per product
Importers Name and address must be included.
Imported By: Bell & Quarry PTY LTD
Unit 8 / 32 Petherick Ave
Hallett Point QLD 4031

also in a Square Box: Made in China

similar to attached Label uploaded. I will also send Die lines to use for designs. The Brand Name is NOT KOLM this is just example of the Label Type Brand is WREN Meadow

Target Market(s)

Supermarkets

Industry/Entity Type

Food

Requirements
Must have
• Image and Product Description

```html
<!DOCTYPE html>
<html lang="en">
<head>
<meta charset="utf-8">
<title>WREN Meadow – Tinned Food Labels</title>
<link href="https://fonts.googleapis.com/css2?family=Merriweather:wght@900&family=Roboto:wght@400;700&display=swap" rel="stylesheet">
<style>
:root{
  --paper:#ffffff;
  --guide:#c9a0a0;
  --guide-text:#8a6a6a;
  --label-dark:#140806;
  --label-mid:#3a120b;
  --label-glow:#6b1a10;
  --band-red:#b3151b;
  --band-deep:#6e0a0e;
  --cream:#f6e3b4;
  --white:#ffffff;
  --text-soft:#e8dcd4;
  --weight-dark:#7a0b0f;
}
*{margin:0;padding:0;box-sizing:border-box}
html,body{width:1200px;height:3000px;overflow:hidden;background:var(--paper)}
body{position:relative;font-family:"Roboto",Arial,sans-serif}

.label-sheet{position:absolute;left:100px;width:1000px;height:420px}
.dim-width{position:absolute;left:0;top:-40px;width:1000px;height:20px;border-left:1px solid var(--guide);border-right:1px solid var(--guide)}
.dim-width::before{content:"";position:absolute;left:0;right:0;top:10px;border-top:1px solid var(--guide)}
.dim-width span{position:absolute;left:50%;top:0;transform:translateX(-50%);background:var(--paper);padding:0 8px;font-size:12px;color:var(--guide-text)}
.dim-height{position:absolute;left:-44px;top:0;width:20px;height:420px;border-top:1px solid var(--guide);border-bottom:1px solid var(--guide)}
.dim-height::before{content:"";position:absolute;top:0;bottom:0;left:10px;border-left:1px solid var(--guide)}
.dim-height span{position:absolute;left:10px;top:50%;transform:translate(-50%,-50%) rotate(-90deg);background:var(--paper);padding:0 8px;font-size:12px;color:var(--guide-text);white-space:nowrap}

.label{position:absolute;inset:0;overflow:hidden;
  background:radial-gradient(ellipse at 50% 100%,var(--label-glow) 0%,var(--label-mid) 35%,var(--label-dark) 80%)}

.importer{position:absolute;left:70px;top:34px;width:290px;text-align:center;color:var(--white);font-weight:700;font-size:17px;line-height:1.35}
.recycle{position:absolute;left:190px;top:180px;width:46px;height:46px}
.origin{position:absolute;left:150px;top:246px;width:126px;border:2px solid var(--white);color:var(--white);font-weight:700;font-size:15px;text-align:center;padding:4px 0}

.center-band{position:absolute;left:390px;top:0;width:220px;height:420px;
  background:linear-gradient(90deg,var(--band-deep) 0%,var(--band-red) 18%,var(--band-red) 82%,var(--band-deep) 100%)}
.brand{position:absolute;left:390px;top:26px;width:220px;text-align:center;font-family:"Merriweather",Georgia,serif;font-weight:900;color:var(--cream);font-size:32px;line-height:1.05}
.ribbon{position:absolute;left:346px;top:128px;width:308px;height:62px}
.ribbon-title{position:absolute;left:346px;top:128px;width:308px;height:52px;display:flex;align-items:center;justify-content:center;font-family:"Merriweather",Georgia,serif;font-weight:900;color:var(--white);font-size:23px;white-space:nowrap}
.product-photo{position:absolute;left:390px;top:196px;width:220px;height:196px}
.weight{position:absolute;left:520px;top:360px;width:84px;text-align:right;color:var(--white);font-weight:700;font-size:20px}
.weight.on-light{color:var(--weight-dark)}

.nutrition{position:absolute;left:672px;top:22px;width:305px;color:var(--white);font-size:10.5px}
.nutrition table{width:100%;border-collapse:collapse;border:1px solid var(--white)}
.nutrition th,.nutrition td{border-bottom:1px solid rgba(255,255,255,.45);padding:2px 5px;text-align:left}
.nutrition th{font-weight:700}
.nutrition td.num,.nutrition th.num{text-align:right}
.nutrition caption{font-weight:700;text-align:left;padding:4px 5px;border:1px solid var(--white);border-bottom:none}
.info{margin-top:12px;color:var(--text-soft);line-height:1.45;font-size:10.5px}
.info b{color:var(--white)}

.photo-veg{background:radial-gradient(circle at 30% 40%,#f2a12a 0%,transparent 30%),radial-gradient(circle at 70% 60%,#f7d23a 0%,transparent 30%),linear-gradient(135deg,#5aa23a,#e07b1c 50%,#e8c73a)}
.photo-peach{background:linear-gradient(160deg,#f7c04a,#e88a23 50%,#b7471a)}
.photo-twofruit{background:linear-gradient(120deg,#d8d26a 0%,#f0e6b8 45%,#e8743a 75%,#b8321e)}
.photo-tomato{background:radial-gradient(circle at 50% 40%,#e8352a 0%,#b3151b 45%,#f4efe8 46%,#ffffff 100%)}
.photo-beans{background:radial-gradient(circle at 50% 50%,#a8461e 0%,#5a2410 45%,#2a1a12 75%,#1a120e)}
</style>
</head>
<body>

<section class="label-sheet" style="top:80px">
  <div class="dim-width"><span>240 mm</span></div>
  <div class="dim-height"><span>100 mm</span></div>
  <div class="label">
    <p class="importer">Imported By:<br>Bell &amp; Quarry PTY LTD<br>Unit 8 / 32 Petherick Ave<br>Hallett Point QLD 4031</p>
    <svg class="recycle" viewBox="0 0 46 46"><circle cx="23" cy="23" r="21" fill="none" stroke="#fff" stroke-width="2"/><path d="M23 10 L34 31 H12 Z" fill="none" stroke="#fff" stroke-width="2.5" stroke-linejoin="round"/></svg>
    <div class="origin">Made in China</div>
    <div class="center-band"></div>
    <p class="brand">WREN<br>Meadow</p>
    <svg class="ribbon" viewBox="0 0 308 62"><path d="M0 14 H28 V62 L14 52 L0 62 Z" fill="#7a0b0f"/><path d="M308 14 H280 V62 L294 52 L308 62 Z" fill="#7a0b0f"/><rect x="16" y="0" width="276" height="52" fill="#c4161c" stroke="#f6e3b4" stroke-width="2"/></svg>
    <div class="ribbon-title">Mixed Vegetables</div>
    <div class="product-photo photo-veg" role="img" aria-label="Photo of peas, diced carrots and corn kernels"></div>
    <p class="weight">425g</p>
    <div class="nutrition">
      <table>
        <caption>NUTRITION INFORMATION</caption>
        <tr><td colspan="3">Servings per package: 4 &nbsp; Serving size: 105g</td></tr>
        <tr><th></th><th class="num">Per Serve</th><th class="num">Per 100g</th></tr>
        <tr><td>Energy</td><td class="num">280kJ</td><td class="num">267kJ</td></tr>
        <tr><td>Protein</td><td class="num">3.1g</td><td class="num">3.0g</td></tr>
        <tr><td>Fat, total</td><td class="num">0.5g</td><td class="num">0.5g</td></tr>
        <tr><td>– saturated</td><td class="num">0.1g</td><td class="num">0.1g</td></tr>
        <tr><td>Carbohydrate</td><td class="num">10.2g</td><td class="num">9.7g</td></tr>
        <tr><td>– sugars</td><td class="num">3.4g</td><td class="num">3.2g</td></tr>
        <tr><td>Sodium</td><td class="num">210mg</td><td class="num">200mg</td></tr>
      </table>
      <p class="info"><b>Ingredients:</b> Peas, Carrots, Corn, Water, Salt.</p>
      <p class="info"><b>Storage Instructions:</b> Once opened, transfer unused contents to a sealed container, refrigerate and use within 3 days.</p>
    </div>
  </div>
</section>

<section class="label-sheet" style="top:660px">
  <div class="dim-width"><span>240 mm</span></div>
  <div class="dim-height"><span>100 mm</span></div>
  <div class="label">
    <p class="importer">Imported By:<br>Bell &amp; Quarry PTY LTD<br>Unit 8 / 32 Petherick Ave<br>Hallett Point QLD 4031</p>
    <svg class="recycle" viewBox="0 0 46 46"><circle cx="23" cy="23" r="21" fill="none" stroke="#fff" stroke-width="2"/><path d="M23 10 L34 31 H12 Z" fill="none" stroke="#fff" stroke-width="2.5" stroke-linejoin="round"/></svg>
    <div class="origin">Made in China</div>
    <div class="center-band"></div>
    <p class="brand">WREN<br>Meadow</p>
    <svg class="ribbon" viewBox="0 0 308 62"><path d="M0 14 H28 V62 L14 52 L0 62 Z" fill="#7a0b0f"/><path d="M308 14 H280 V62 L294 52 L308 62 Z" fill="#7a0b0f"/><rect x="16" y="0" width="276" height="52" fill="#c4161c" stroke="#f6e3b4" stroke-width="2"/></svg>
    <div class="ribbon-title">Sliced Peaches</div>
    <div class="product-photo photo-peach" role="img" aria-label="Photo of golden sliced peaches"></div>
    <p class="weight">820g</p>
    <div class="nutrition">
      <table>
        <caption>NUTRITION INFORMATION</caption>
        <tr><td colspan="3">Servings per package: 8 &nbsp; Serving size: 102g</td></tr>
        <tr><th></th><th class="num">Per Serve</th><th class="num">Per 100g</th></tr>
        <tr><td>Energy</td><td class="num">310kJ</td><td class="num">304kJ</td></tr>
        <tr><td>Protein</td><td class="num">0.5g</td><td class="num">0.5g</td></tr>
        <tr><td>Fat, total</td><td class="num">0.1g</td><td class="num">0.1g</td></tr>
        <tr><td>– saturated</td><td class="num">0.0g</td><td class="num">0.0g</td></tr>
        <tr><td>Carbohydrate</td><td class="num">17.6g</td><td class="num">17.3g</td></tr>
        <tr><td>– sugars</td><td class="num">16.8g</td><td class="num">16.5g</td></tr>
        <tr><td>Sodium</td><td class="num">5mg</td><td class="num">5mg</td></tr>
      </table>
      <p class="info"><b>Ingredients:</b> Peaches, Water, Sugar, Citric Acid.</p>
      <p class="info"><b>Storage Instructions:</b> Once opened, transfer unused contents to a sealed container, refrigerate and use within 3 days.</p>
    </div>
  </div>
</section>

<section class="label-sheet" style="top:1240px">
  <div class="dim-width"><span>240 mm</span></div>
  <div class="dim-height"><span>100 mm</span></div>
  <div class="label">
    <p class="importer">Imported By:<br>Bell &amp; Quarry PTY LTD<br>Unit 8 / 32 Petherick Ave<br>Hallett Point QLD 4031</p>
    <svg class="recycle" viewBox="0 0 46 46"><circle cx="23" cy="23" r="21" fill="none" stroke="#fff" stroke-width="2"/><path d="M23 10 L34 31 H12 Z" fill="none" stroke="#fff" stroke-width="2.5" stroke-linejoin="round"/></svg>
    <div class="origin">Made in China</div>
    <div class="center-band"></div>
    <p class="brand">WREN<br>Meadow</p>
    <svg class="ribbon" viewBox="0 0 308 62"><path d="M0 14 H28 V62 L14 52 L0 62 Z" fill="#7a0b0f"/><path d="M308 14 H280 V62 L294 52 L308 62 Z" fill="#7a0b0f"/><rect x="16" y="0" width="276" height="52" fill="#c4161c" stroke="#f6e3b4" stroke-width="2"/></svg>
    <div class="ribbon-title">Two Fruits</div>
    <div class="product-photo photo-twofruit" role="img" aria-label="Photo of a halved pear and peaches, labelled Peach &amp; Pear"></div>
    <p class="weight">820g</p>
    <div class="nutrition">
      <table>
        <caption>NUTRITION INFORMATION</caption>
        <tr><td colspan="3">Servings per package: 8 &nbsp; Serving size: 102g</td></tr>
        <tr><th></th><th class="num">Per Serve</th><th class="num">Per 100g</th></tr>
        <tr><td>Energy</td><td class="num">295kJ</td><td class="num">289kJ</td></tr>
        <tr><td>Protein</td><td class="num">0.4g</td><td class="num">0.4g</td></tr>
        <tr><td>Fat, total</td><td class="num">0.1g</td><td class="num">0.1g</td></tr>
        <tr><td>– saturated</td><td class="num">0.0g</td><td class="num">0.0g</td></tr>
        <tr><td>Carbohydrate</td><td class="num">16.9g</td><td class="num">16.6g</td></tr>
        <tr><td>– sugars</td><td class="num">15.7g</td><td class="num">15.4g</td></tr>
        <tr><td>Sodium</td><td class="num">6mg</td><td class="num">6mg</td></tr>
      </table>
      <p class="info"><b>Ingredients:</b> Peach, Pear, Water, Sugar, Antioxidant.</p>
      <p class="info"><b>Storage Instructions:</b> Once opened, transfer unused contents to a sealed container, refrigerate and use within 3 days.</p>
    </div>
  </div>
</section>

<section class="label-sheet" style="top:1820px">
  <div class="dim-width"><span>240 mm</span></div>
  <div class="dim-height"><span>100 mm</span></div>
  <div class="label">
    <p class="importer">Imported By:<br>Bell &amp; Quarry PTY LTD<br>Unit 8 / 32 Petherick Ave<br>Hallett Point QLD 4031</p>
    <svg class="recycle" viewBox="0 0 46 46"><circle cx="23" cy="23" r="21" fill="none" stroke="#fff" stroke-width="2"/><path d="M23 10 L34 31 H12 Z" fill="none" stroke="#fff" stroke-width="2.5" stroke-linejoin="round"/></svg>
    <div class="origin">Made in China</div>
    <div class="center-band"></div>
    <p class="brand">WREN<br>Meadow</p>
    <svg class="ribbon" viewBox="0 0 308 62"><path d="M0 14 H28 V62 L14 52 L0 62 Z" fill="#7a0b0f"/><path d="M308 14 H280 V62 L294 52 L308 62 Z" fill="#7a0b0f"/><rect x="16" y="0" width="276" height="52" fill="#c4161c" stroke="#f6e3b4" stroke-width="2"/></svg>
    <div class="ribbon-title">Diced Tomato's</div>
    <div class="product-photo photo-tomato" role="img" aria-label="Photo of whole and diced red tomatoes"></div>
    <p class="weight on-light">425g</p>
    <div class="nutrition">
      <table>
        <caption>NUTRITION INFORMATION</caption>
        <tr><td colspan="3">Servings per package: 4 &nbsp; Serving size: 105g</td></tr>
        <tr><th></th><th class="num">Per Serve</th><th class="num">Per 100g</th></tr>
        <tr><td>Energy</td><td class="num">95kJ</td><td class="num">90kJ</td></tr>
        <tr><td>Protein</td><td class="num">1.2g</td><td class="num">1.1g</td></tr>
        <tr><td>Fat, total</td><td class="num">0.2g</td><td class="num">0.2g</td></tr>
        <tr><td>– saturated</td><td class="num">0.0g</td><td class="num">0.0g</td></tr>
        <tr><td>Carbohydrate</td><td class="num">3.5g</td><td class="num">3.3g</td></tr>
        <tr><td>– sugars</td><td class="num">3.0g</td><td class="num">2.9g</td></tr>
        <tr><td>Sodium</td><td class="num">160mg</td><td class="num">152mg</td></tr>
      </table>
      <p class="info"><b>Ingredients:</b> Tomatoes, Tomato Juice, Citric Acid.</p>
      <p class="info"><b>Storage Instructions:</b> Once opened, transfer unused contents to a sealed container, refrigerate and use within 3 days.</p>
    </div>
  </div>
</section>

<section class="label-sheet" style="top:2400px">
  <div class="dim-width"><span>240 mm</span></div>
  <div class="dim-height"><span>100 mm</span></div>
  <div class="label">
    <p class="importer">Imported By:<br>Bell &amp; Quarry PTY LTD<br>Unit 8 / 32 Petherick Ave<br>Hallett Point QLD 4031</p>
    <svg class="recycle" viewBox="0 0 46 46"><circle cx="23" cy="23" r="21" fill="none" stroke="#fff" stroke-width="2"/><path d="M23 10 L34 31 H12 Z" fill="none" stroke="#fff" stroke-width="2.5" stroke-linejoin="round"/></svg>
    <div class="origin">Made in China</div>
    <div class="center-band"></div>
    <p class="brand">WREN<br>Meadow</p>
    <svg class="ribbon" viewBox="0 0 308 62"><path d="M0 14 H28 V62 L14 52 L0 62 Z" fill="#7a0b0f"/><path d="M308 14 H280 V62 L294 52 L308 62 Z" fill="#7a0b0f"/><rect x="16" y="0" width="276" height="52" fill="#c4161c" stroke="#f6e3b4" stroke-width="2"/></svg>
    <div class="ribbon-title">Baked Beans</div>
    <div class="product-photo photo-beans" role="img" aria-label="Photo of baked beans in tomato sauce in a dark bowl"></div>
    <p class="weight">425g</p>
    <div class="nutrition">
      <table>
        <caption>NUTRITION INFORMATION</caption>
        <tr><td colspan="3">Servings per package: 2 &nbsp; Serving size: 210g</td></tr>
        <tr><th></th><th class="num">Per Serve</th><th class="num">Per 100g</th></tr>
        <tr><td>Energy</td><td class="num">710kJ</td><td class="num">338kJ</td></tr>
        <tr><td>Protein</td><td class="num">9.8g</td><td class="num">4.7g</td></tr>
        <tr><td>Fat, total</td><td class="num">0.8g</td><td class="num">0.4g</td></tr>
        <tr><td>– saturated</td><td class="num">0.1g</td><td class="num">0.1g</td></tr>
        <tr><td>Carbohydrate</td><td class="num">27.3g</td><td class="num">13.0g</td></tr>
        <tr><td>– sugars</td><td class="num">10.5g</td><td class="num">5.0g</td></tr>
        <tr><td>Sodium</td><td class="num">790mg</td><td class="num">376mg</td></tr>
      </table>
      <p class="info"><b>Ingredients:</b> Beans, Tomato Sauce, Sugar, Salt.</p>
      <p class="info"><b>Storage Instructions:</b> Once opened, transfer unused contents to a sealed container, refrigerate and use within 3 days.</p>
    </div>
  </div>
</section>

</body>
</html>
```